KRL Stationery Design Project

Dear Designers,
We need a new stationery design for company to match our new logo.
Designers should provide a design for the following:
1. Business Card: 3.5x2 Inches.
2. Letterhead: A4 size.
3. Envelops: 25x35.5 Cm.
You can keep the Arabic name at the bottom of the logo Or you can use the separate attached Arabic Name.
Please refer to the attached logo guide for design information.
Sample Business Card information:
Name: Tarek Sowan
Position: Operation Manager
Tel: +966 920007164 Ex. 500
Fax: +966 (3)8842617
Mob: +966 (5)00263817
email: tarek@krl-example.com.sa
URL: www.krl-example.com.sa
Address:
Nakheel Heights, Suite 718
Zayed bin Omar Str.
Khobar, 31847
Saudi Arabia
Updates
Dear All,
Please note, we had uploaded our logo along with Arabic writing in Adobe illustrator format (.ai).
Regards,
Karim
Dear All,
A sample data for the business card had been added as per your request.
Regards,
Karim

```html
<!DOCTYPE html>
<html lang="en">
<head>
<meta charset="utf-8">
<title>KRL Business Card</title>
<link rel="stylesheet" href="https://fonts.googleapis.com/css2?family=Source+Sans+3:ital,wght@0,400;0,600;0,700;1,700&display=swap">
<style>
  :root {
    --backdrop: #1f1f1f;
    --card: #ffffff;
    --navy: #14305a;
    --grey: #97999c;
    --ink-light: #ffffff;
    --card-radius: 28px;
    --card-shadow: 0 6px 18px rgba(0,0,0,0.55);
  }
  * { box-sizing: border-box; margin: 0; padding: 0; }
  html, body {
    width: 960px;
    height: 1200px;
    overflow: hidden;
    background: var(--backdrop);
    font-family: "Source Sans 3", "Myriad Pro", Arial, sans-serif;
  }
  .canvas { position: relative; width: 960px; height: 1200px; }
  .card {
    position: absolute;
    width: 840px;
    height: 480px;
    background: var(--card);
    border-radius: var(--card-radius);
    box-shadow: var(--card-shadow);
    overflow: hidden;
  }
  .card--front { left: 60px; top: 68px; }
  .card--back  { left: 57px; top: 625px; }
  .card__waves { position: absolute; inset: 0; width: 840px; height: 480px; }

  .brand {
    position: absolute;
    display: flex;
    align-items: center;
    gap: 18px;
    color: var(--navy);
    font-weight: 700;
    line-height: 1;
  }
  .brand__mark { background: var(--navy); display: block; }
  .card--front .brand { left: 50px; top: 80px; font-size: 104px; letter-spacing: 2px; }
  .card--front .brand__mark { width: 34px; height: 34px; }
  .card--back .brand { left: 0; right: 0; top: 160px; justify-content: center; font-size: 150px; letter-spacing: 3px; }
  .card--back .brand__mark { width: 48px; height: 48px; }

  .person {
    position: absolute;
    left: 37px;
    top: 284px;
    color: var(--navy);
    font-size: 27px;
    font-weight: 400;
  }
  .person__role { font-size: 21px; }
  .phones {
    position: absolute;
    left: 37px;
    top: 334px;
    color: var(--navy);
    font-size: 19px;
  }
  .footer-info {
    position: absolute;
    left: 0;
    right: 0;
    top: 410px;
    padding-left: 60px;
    text-align: center;
    color: var(--ink-light);
    font-size: 19px;
    line-height: 30px;
  }
  .footer-info b { font-style: italic; font-weight: 700; }
</style>
</head>
<body>
<main class="canvas">

  <section class="card card--front" aria-label="Business card front">
    <svg class="card__waves" viewBox="0 0 840 480" aria-hidden="true">
      <path d="M690 0 L840 0 L840 150 Q 690 330 500 378 Q 730 250 690 0 Z" fill="var(--grey)"/>
      <path d="M0 418 Q 70 396 260 386 Q 620 368 840 162 L840 480 L0 480 Z" fill="var(--navy)"/>
    </svg>

    <div class="brand"><span class="brand__mark"></span>KRL</div>

    <p class="person">Your Name - <span class="person__role">Designation</span></p>
    <p class="phones">t : 123-123-1234&nbsp; : &nbsp;f : 123-123-1234</p>

    <div class="footer-info">
      <p><b>e</b> : tarek@krl-example.com.sa &nbsp;|&nbsp; <b>w</b> : www.krl-example.com.sa</p>
      <p>1234, Suite# 123, Street Name, State Name, Country Code</p>
    </div>
  </section>

  <section class="card card--back" aria-label="Business card back">
    <div class="brand"><span class="brand__mark"></span>KRL</div>
  </section>

</main>
</body>
</html>
```